Medical Billing Company Needs a Business Card Design

We need a business card design for a Florida based medical billing company called 'Clinicians Keystone Solutions'. We specialize in providing revenue cycle management services to physician and therapist offices (we're basically their back-office processing partner for providing billing software, claims submissions, A/R follow-up and patient statements & collections. Our logo is red and blue-ish, so make sure that whatever other elements are used will match appropriately. Our current business card design has a too small font size. I'd like to project an image that shows we are modern & reliable. On a side note, I'm planning on using ZUB for printing these cards.

Target Market(s)

Office managers, physicians, therapists

Industry/Entity Type

Printing

Requirements
Must have
• Logo
Name of Employee
Phone
Fax
E-mail
Website

```html
<!DOCTYPE html>
<html lang="en">
<head>
<meta charset="utf-8">
<title>Clinicians Keystone Solutions – Business Cards</title>
<link rel="stylesheet" href="https://fonts.googleapis.com/css2?family=Source+Sans+3:wght@400;600;700&display=swap">
<style>
  :root {
    --navy: #2b2a7a;
    --red: #b3262c;
    --grey: #555558;
    --paper: #ffffff;
    --stage: #eceae6;
    --rule: #c9c9cc;
  }
  * { box-sizing: border-box; margin: 0; padding: 0; }
  html, body { width: 1200px; height: 720px; overflow: hidden; }
  body {
    background: var(--stage);
    font-family: "Source Sans 3", sans-serif;
    display: flex;
    align-items: center;
    justify-content: center;
    gap: 60px;
  }
  .card {
    position: relative;
    width: 520px;
    height: 297px;
    background: var(--paper);
    box-shadow: 0 2px 10px rgba(0,0,0,0.12);
  }
  /* Front */
  .brand-name {
    position: absolute;
    top: 58px;
    left: 0;
    right: 0;
    text-align: center;
    font-size: 27px;
    font-weight: 400;
    letter-spacing: 1.5px;
    color: var(--navy);
  }
  .person {
    position: absolute;
    top: 142px;
    right: 276px;
    text-align: right;
  }
  .person-name {
    font-size: 17px;
    font-weight: 700;
    color: var(--navy);
    line-height: 1.1;
  }
  .person-title {
    font-size: 12px;
    color: var(--red);
    margin-bottom: 12px;
  }
  .person-address {
    font-size: 13px;
    color: var(--grey);
    line-height: 1.3;
  }
  .divider {
    position: absolute;
    top: 130px;
    left: 258px;
    width: 1px;
    height: 92px;
    background: var(--rule);
  }
  .contacts {
    position: absolute;
    top: 130px;
    left: 270px;
    list-style: none;
  }
  .contacts li {
    display: flex;
    align-items: center;
    gap: 6px;
    font-size: 13px;
    color: var(--grey);
    height: 22px;
  }
  .contacts svg { width: 12px; height: 12px; flex: none; }
  /* Back */
  .back-mark {
    position: absolute;
    top: 100px;
    left: 0;
    right: 0;
    text-align: center;
    font-size: 30px;
    font-weight: 400;
    letter-spacing: 1.5px;
    color: var(--navy);
  }
  .back-web {
    position: absolute;
    bottom: 42px;
    left: 0;
    right: 0;
    text-align: center;
    font-size: 17px;
    letter-spacing: 0.8px;
    color: var(--navy);
  }
</style>
</head>
<body>
  <section class="card card-front">
    <div class="brand-name">CLINICIANS KEYSTONE</div>
    <div class="person">
      <div class="person-name">Your Name</div>
      <div class="person-title">Title</div>
      <div class="person-address">Street Name, City Name<br>State Zip Code</div>
    </div>
    <div class="divider"></div>
    <ul class="contacts">
      <li>
        <svg viewBox="0 0 12 12" aria-hidden="true"><circle cx="6" cy="6" r="6" fill="var(--grey)"/><path d="M4 3.2c-.6.4-.6 1.6.4 3s2.2 2.4 3 2.2l.7-.8-1.2-.9-.6.5c-.6-.3-1.2-1-1.5-1.6l.5-.6-.8-1.2z" fill="#fff"/></svg>
        123-456-0789
      </li>
      <li>
        <svg viewBox="0 0 12 12" aria-hidden="true"><rect x="3.5" y="1" width="5" height="10" rx="1" fill="var(--grey)"/><rect x="4.3" y="2.2" width="3.4" height="5.5" fill="#fff"/></svg>
        123-456-0789
      </li>
      <li>
        <svg viewBox="0 0 12 12" aria-hidden="true"><circle cx="6" cy="6" r="6" fill="var(--grey)"/><rect x="2.8" y="3.8" width="6.4" height="4.4" fill="#fff"/><path d="M2.8 3.8l3.2 2.4 3.2-2.4" fill="none" stroke="var(--grey)" stroke-width=".7"/></svg>
        info@clinicianskeystone.com
      </li>
      <li>
        <svg viewBox="0 0 12 12" aria-hidden="true"><circle cx="6" cy="6" r="6" fill="var(--grey)"/><circle cx="6" cy="6" r="3.4" fill="none" stroke="#fff" stroke-width=".8"/><path d="M2.6 6h6.8M6 2.6v6.8" stroke="#fff" stroke-width=".6"/></svg>
        www.clinicianskeystone.com
      </li>
    </ul>
  </section>

  <section class="card card-back">
    <div class="back-mark">CLINICIANS KEYSTONE</div>
    <div class="back-web">www.clinicianskeystone.com</div>
  </section>
</body>
</html>
```